IT company developing solutions for air cargo industry is looking for a new website

We are a professional IT company developing solutions for air cargo industry worldwide.

We are looking to update and completely redesign our current webpages: https://www.brisklane.cz/

What we like about our current pages are the animated graphics on the home page. These could stay, but not a must.

The design of the new pages should be very modern, clean, unique, creative, professional, and to make a statement. We are looking for animated graphics, cool and interesting interactions, cascading layers, etc.

Our company logo is yellow, gray and black. You don’t necessarily have to stick to this colour scheme, however the corporate colors should work well with the overal design of the web pages.
Dark mode pages are also an option.

The scope of the project would include creating a:

• Header
• Footer
• Landing page
• Navigation bar (8 tabs)
• Subpages (10)

In the first stage we are looking only for the header / footer / landing page with navigaton bar / Solutions page design.
As a second round, finalists might be asked to submit another section of the website to see their consistency in terms of the look and feel proposed for the Homepage and Solutions’ pages.
The winning designer will then complete the rest of the pages.

Attached you will find a brief for the first scope of the project. Please read the note section on slide nr. 3 carefully to understand, what we exactly are looking for to achieve.

Industry/Entity Type

Aviation

Number of Pages Required

1 page

Requirements
Must have
• See brief
Nice to have
• See brief
Should not have
• See brief

```html
<!DOCTYPE html>
<html lang="en">
<head>
<meta charset="utf-8">
<title>Brisk Lane – Air Cargo IT Solutions</title>
<link rel="stylesheet" href="https://fonts.googleapis.com/css2?family=Oxanium:wght@400;500;600&family=Nunito:wght@400;600;700;800&display=swap">
<style>
:root{
  --yellow:#fcc20a;
  --ink:#111111;
  --grey:#7d7d7d;
  --pale:#fdf3d6;
  --line:#cfcfcf;
  --footer:#000000;
  --sky-top:#6fa9e0;
  --sky-bottom:#f4f8fc;
}
*{margin:0;padding:0;box-sizing:border-box}
html,body{width:808px;height:1200px;overflow:hidden;background:#fff}
body{position:relative;font-family:'Nunito',sans-serif;color:var(--ink)}
.abs{position:absolute}

/* header */
.site-header{left:0;top:0;width:808px;height:70px;background:#fff}
.brand{left:89px;top:24px;display:flex;align-items:center;gap:6px;font-weight:700;font-size:16px;color:#555}
.brand-mark{width:14px;height:14px;background:var(--yellow)}
.main-nav{left:264px;top:28px;display:flex;gap:15.6px;font-size:10px;font-weight:600;color:var(--ink)}

/* hero */
.hero{left:0;top:70px;width:808px;height:477px;background:linear-gradient(180deg,var(--sky-top) 0%,#a9ccef 35%,#dfeaf6 75%,var(--sky-bottom) 100%)}
.hero-title{left:73px;top:127px;width:320px;font-family:'Oxanium',sans-serif;font-weight:500;font-size:30px;line-height:36.6px;color:var(--ink);white-space:nowrap}
.hero-text{left:75px;top:300px;width:280px;font-size:11px;line-height:17.2px;color:#1e1e1e;white-space:nowrap}
.btn{left:77px;top:409px;width:102px;height:36px;background:var(--yellow);display:flex;align-items:center;justify-content:center;font-weight:800;font-size:9.4px;color:var(--ink);letter-spacing:.2px}
.globe{left:381px;top:115px;width:374px;height:374px;border-radius:50%;background:radial-gradient(circle at 45% 40%,#3a6fc1 0%,#1d3f8f 55%,#0e2463 100%);box-shadow:0 8px 30px rgba(20,40,90,.25)}

/* statement */
.statement-top{left:183px;top:543px;width:453px;height:39px;background:var(--grey);display:flex;align-items:center;justify-content:center;font-family:'Oxanium',sans-serif;font-weight:500;font-size:16.6px;color:#fff}
.statement-bottom{left:197px;top:582px;width:425px;height:40px;background:var(--yellow);display:flex;align-items:center;justify-content:center;font-family:'Oxanium',sans-serif;font-weight:500;font-size:16.6px;color:#fff}

/* facts */
.facts{left:86px;top:674px;width:632px;height:167px;border:1.5px solid var(--line)}
.facts-title{left:366px;top:663px;width:76px;background:#fff;text-align:center;font-family:'Oxanium',sans-serif;font-weight:500;font-size:16px;color:var(--ink)}
.fact{top:718px;text-align:center}
.fact-icon{width:30px;height:30px;border-radius:50%;background:var(--pale);margin:0 auto;display:flex;align-items:center;justify-content:center}
.fact-num{margin-top:12px;font-family:'Oxanium',sans-serif;font-size:12.8px;color:var(--ink)}
.fact-label{margin-top:3px;font-size:9.3px;line-height:14px;color:#333}
.divider{top:703px;width:1px;height:119px;background:#e3e3e3}

/* tagline */
.aircraft{left:48px;top:872px;width:110px;height:34px;background:linear-gradient(90deg,#e8ecf0,#c9ced4);border-radius:18px 6px 6px 18px}
.tagline{left:184px;top:907px;width:540px;height:43px;background:var(--yellow);display:flex;align-items:center;justify-content:center;font-family:'Oxanium',sans-serif;font-weight:500;font-size:14.6px;color:var(--ink);z-index:2}

/* footer */
.site-footer{left:0;top:934px;width:808px;height:266px;background:var(--footer)}
.footer-brand{left:89px;top:1030px;display:flex;align-items:center;gap:10px;font-weight:700;font-size:28px;color:#6b6b6b}
.footer-brand .brand-mark{width:22px;height:22px}
.footer-col{top:986px;color:#fff}
.footer-col h4{font-family:'Oxanium',sans-serif;font-weight:600;font-size:9.8px;margin-bottom:6px;letter-spacing:.2px}
.footer-col li{list-style:none;font-size:7.6px;line-height:14px;color:#e8e8e8}
.footer-rule{left:88px;top:1132px;width:630px;height:1px;background:#333}
.copyright{left:0;top:1161px;width:808px;text-align:center;font-size:7.6px;color:#e8e8e8}
</style>
</head>
<body>

<header class="abs site-header">
  <div class="abs brand"><span>Brisk Lane</span><span class="brand-mark"></span></div>
  <nav class="abs main-nav">
    <span>Industries</span><span>Solutions</span><span>Operational Support</span><span>Case Studies</span><span>Testimonials</span><span>News</span><span>About Us</span>
  </nav>
</header>

<section class="abs hero"></section>
<h1 class="abs hero-title">Seamlessly<br>connecting the air<br>cargo industry from<br>Manila to Tahiti</h1>
<p class="abs hero-text">Blending decades of air cargo knowledge with<br>end-to-end IT solutions. Whether you are an Airline,<br>GSA, GHA, Forwarder or E-commerce Operator, our<br>expertise can elevate your daily workflows, cutting<br>down on expenses, time, and errors.</p>
<div class="abs btn">LEARN MORE</div>
<div class="abs globe" role="img" aria-label="Globe showing Australia and the Pacific with a flight route from Manila to Tahiti"></div>

<svg class="abs" style="left:0;top:0" width="808" height="1200" viewBox="0 0 1500 2229" aria-hidden="true">
  <path d="M358 972 L405 966 L398 974 Z M372 968 L386 960 L392 966 Z M380 976 L388 988 L376 980 Z" fill="#555"/>
  <ellipse cx="308" cy="1685" rx="55" ry="19" fill="none" stroke="#1a2a55" stroke-width="1.5"/>
</svg>

<div class="abs statement-top">We are not IT tech experts attempting to do cargo!</div>
<div class="abs statement-bottom">We are cargo experts with programming skills!</div>

<section class="abs facts"></section>
<h2 class="abs facts-title">FACTS</h2>
<div class="abs divider" style="left:171px"></div>
<div class="abs divider" style="left:249px"></div>
<div class="abs divider" style="left:380px"></div>
<div class="abs divider" style="left:489px"></div>
<div class="abs divider" style="left:598px"></div>

<div class="abs fact" style="left:96px;width:72px">
  <div class="fact-icon"><svg width="18" height="14" viewBox="0 0 18 14"><path d="M2 8 L15 3 M6 7 L9 2 M1 12 H17" stroke="#111" stroke-width="1.2" fill="none"/></svg></div>
  <div class="fact-num">2014</div><div class="fact-label">Established</div>
</div>
<div class="abs fact" style="left:173px;width:72px">
  <div class="fact-icon"><svg width="20" height="14" viewBox="0 0 20 14"><circle cx="4" cy="4" r="2" fill="none" stroke="#111"/><circle cx="10" cy="3" r="2" fill="none" stroke="#111"/><circle cx="16" cy="4" r="2" fill="none" stroke="#111"/><path d="M1 12 Q4 7 7 12 M7 12 Q10 6 13 12 M13 12 Q16 7 19 12" fill="none" stroke="#111"/></svg></div>
  <div class="fact-num">22</div><div class="fact-label">Employees</div>
</div>
<div class="abs fact" style="left:252px;width:126px">
  <div class="fact-icon"><svg width="18" height="14" viewBox="0 0 18 14"><path d="M2 6 V4 H15 M12 1 L15 4 L12 7 M16 8 V10 H3 M6 7 L3 10 L6 13" fill="none" stroke="#111" stroke-width="1.3"/></svg></div>
  <div class="fact-num">11,500,000 +</div><div class="fact-label">Nr. of Annual Electronic<br>Exchanges</div>
</div>
<div class="abs fact" style="left:383px;width:104px">
  <div class="fact-icon"><svg width="18" height="18" viewBox="0 0 18 18"><circle cx="9" cy="9" r="7" fill="none" stroke="#111" stroke-width="1.2"/><path d="M2 9 H16 M9 2 Q5 9 9 16 Q13 9 9 2" fill="none" stroke="#111"/></svg></div>
  <div class="fact-num">18</div><div class="fact-label">Countries covered</div>
</div>
<div class="abs fact" style="left:492px;width:104px">
  <div class="fact-icon"><svg width="18" height="18" viewBox="0 0 18 18"><circle cx="9" cy="9" r="2.5" fill="none" stroke="#111"/><circle cx="3" cy="4" r="2" fill="none" stroke="#111"/><circle cx="15" cy="4" r="2" fill="none" stroke="#111"/><circle cx="3" cy="14" r="2" fill="none" stroke="#111"/><circle cx="15" cy="14" r="2" fill="none" stroke="#111"/><path d="M4.5 5.5 L7 7.5 M13.5 5.5 L11 7.5 M4.5 12.5 L7 10.5 M13.5 12.5 L11 10.5" stroke="#111"/></svg></div>
  <div class="fact-num">20+</div><div class="fact-label">Connected Clients</div>
</div>
<div class="abs fact" style="left:602px;width:114px">
  <div class="fact-icon"><svg width="18" height="18" viewBox="0 0 18 18"><rect x="2" y="3" width="14" height="13" rx="1.5" fill="none" stroke="#111" stroke-width="1.2"/><path d="M2 6.5 H16" stroke="#111"/><circle cx="5.5" cy="9.5" r="1" fill="#111"/><circle cx="9" cy="9.5" r="1" fill="#111"/><circle cx="12.5" cy="9.5" r="1" fill="#111"/><circle cx="5.5" cy="13" r="1" fill="#111"/><circle cx="9" cy="13" r="1" fill="#111"/></svg></div>
  <div class="fact-num">350,000 +</div><div class="fact-label">Nr. of Annual AWBs</div>
</div>

<footer class="abs site-footer"></footer>
<div class="abs aircraft" role="img" aria-label="White passenger jet flying towards the slogan band"></div>
<div class="abs tagline">Affordable IT Solutions That Revolutionize Tomorrow’s Air Cargo Today</div>

<div class="abs footer-brand"><span>Brisk Lane</span><span class="brand-mark"></span></div>
<div class="abs footer-col" style="left:371px">
  <h4>MENU</h4>
  <ul><li>Industries</li><li>Solutions</li><li>Operational Support</li><li>Case Studies</li><li>Testimonials</li><li>News</li><li>About Us</li></ul>
</div>
<div class="abs footer-col" style="left:496px">
  <h4>SOLUTIONS</h4>
  <ul><li>Aerolink Airline</li><li>Aerolink GHA</li><li>WayBill One</li><li>RoadLink Cargo</li><li>Hive Portal</li></ul>
</div>
<div class="abs footer-col" style="left:610px">
  <h4>ABOUT US</h4>
  <ul><li>About brisk lane Our story</li><li>Our ethos</li><li>Sustainability</li><li>Contact</li></ul>
</div>
<div class="abs footer-rule"></div>
<p class="abs copyright">Copyright © 2024 All Rights Reserved</p>

</body>
</html>
```